Transform Your Giving

I need a tri-fold brochure that will fit in a standard number 10 business envelope. Meadowlark and Allied Services is a charitable nonprofit. The goal of this brochure is to stimulate people into thinking about other ways to make a donation. The design should communicate the essential information on donation options, create a sense of professional integrity, be graphically sharp, easy to read and laid out in a way that doesn't make the material appear crowded.

```html
<!DOCTYPE html>
<html lang="en">
<head>
<meta charset="utf-8">
<title>Transform Your Giving – Tri-fold Brochure</title>
<link rel="stylesheet" href="https://fonts.googleapis.com/css2?family=Montserrat:ital,wght@0,300;0,400;0,500;0,600;0,700;0,800;1,400&display=swap">
<style>
:root{
  --stage:#969696;
  --navy:#2b286f;
  --green:#4cb748;
  --white:#ffffff;
  --paper:#efeff1;
  --paper-mid:#e7e7ea;
  --ink:#3a3a48;
}
*{margin:0;padding:0;box-sizing:border-box}
html,body{width:1200px;height:1200px;overflow:hidden;background:var(--stage)}
body{font-family:"Montserrat",sans-serif;position:relative;color:var(--ink)}
ul{list-style:none}
.spread{position:absolute;overflow:hidden}
.spread-outside{left:251px;top:60px;width:675px;height:525px;background:var(--white)}
.spread-inside{left:250px;top:616px;width:677px;height:526px;background:var(--paper)}
.shapes{position:absolute;left:0;top:0}
.abs{position:absolute}

/* brand name */
.brand{position:absolute;text-align:center;color:var(--navy);font-weight:800;line-height:1.05}
.brand .dot{display:block;width:9px;height:9px;border-radius:50%;background:var(--green);margin:0 auto 4px}
.brand-name{font-size:9.5px;letter-spacing:.3px}

/* outside – left panel */
.impact-title{left:0;width:222px;top:22px;font-weight:800;font-size:15px;line-height:19px;text-align:center;color:var(--navy)}
.impact-title span{color:var(--green);display:block}
.impact-intro{left:16px;width:190px;top:71px;font-size:8.4px;line-height:10.1px;text-align:center;color:#33334a}
.option{position:absolute;left:45px;width:135px;height:16px;border:1px solid var(--green);font-size:8.6px;color:#33334a;display:flex;align-items:center;justify-content:center;gap:4px}
.option svg{width:8px;height:8px}

/* outside – middle panel */
.learn-more{left:250px;width:178px;top:76px;font-size:8.2px;line-height:10.2px;text-align:center;color:#3a3a55;font-weight:500}
.quote{left:238px;width:200px;top:253px;font-style:italic;font-size:9px;line-height:11px;color:var(--white);text-align:center}
.quote-author{left:238px;width:200px;top:277px;font-size:7.8px;color:var(--green);text-align:center;font-weight:500}
.will-lead{left:238px;width:200px;top:303px;font-size:8.6px;color:var(--white);text-align:center;font-weight:500}
.will-link{left:218px;width:240px;top:313px;font-size:13px;color:var(--green);text-align:center;font-weight:800}
.will-note{left:238px;width:200px;top:331px;font-size:8.6px;color:var(--white);text-align:center;font-weight:300}
.will-free{left:238px;width:200px;top:341px;font-size:9.6px;color:var(--white);text-align:center;font-weight:800}
.contact-btn{left:286px;top:365px;width:99px;height:17px;border-radius:9px;background:var(--green);color:var(--white);font-weight:800;font-size:10.5px;display:flex;align-items:center;justify-content:center;letter-spacing:.3px}
.question{left:238px;width:200px;top:387px;font-size:11px;color:var(--white);text-align:center;font-weight:800}
.question-note{left:238px;width:200px;top:400px;font-size:8.4px;line-height:10.5px;color:var(--white);text-align:center;font-weight:400}
.contact-col{top:436px;font-size:6.5px;line-height:8.1px;color:var(--white);font-weight:500}
.follow{left:238px;width:200px;top:468px;font-size:8px;color:var(--white);text-align:center;font-weight:500;display:flex;justify-content:center;align-items:center;gap:3px}
.follow i{display:inline-block;width:9px;height:9px;border-radius:50%}
.disclaimer{left:243px;width:190px;top:486px;font-size:4.1px;line-height:5px;color:#d9d8ee;text-align:center}

/* outside – right panel */
.hex-label{position:absolute;width:60px;text-align:center;color:var(--white);font-size:5.4px;font-weight:700;line-height:6.4px}
.transform{left:440px;width:232px;top:400px;text-align:center;color:var(--white);font-weight:800;font-size:18px;letter-spacing:.4px}
.your-giving{left:440px;width:232px;top:416px;text-align:center;color:var(--green);font-weight:800;font-size:26px;letter-spacing:.3px}
.mottos{left:445px;width:224px;top:456px;display:flex;justify-content:center;gap:10px;color:var(--white);font-weight:700;font-size:11.5px}
.mottos span{display:flex;align-items:center;gap:4px}
.mottos svg{width:13px;height:13px}
.discover{left:445px;width:224px;top:480px;text-align:center;color:var(--white);font-weight:600;font-size:8.3px;line-height:10.5px}

/* inside */
.headline-number{left:48px;top:39px;font-weight:800;color:var(--green);font-size:76px;line-height:76px;transform:scaleX(.82);transform-origin:left top}
.headline-badge{left:95px;top:49px;font-weight:800;color:var(--white);font-size:19.5px;line-height:19px;letter-spacing:0}
.way-title{position:absolute;color:var(--navy);font-weight:700;font-size:11px;line-height:13.5px}
.way-hint{position:absolute;color:var(--green);font-weight:700;font-size:5.6px;line-height:7.3px}
.way-body{position:absolute;color:#3b3b48;font-size:5.55px;line-height:7.3px}
.how-pill{position:absolute;height:11px;padding:0 5px;border-radius:6px;background:var(--green);color:var(--white);font-size:6px;font-weight:500;display:flex;align-items:center}
.inside-brand{left:223px;width:223px;top:476px}
.inside-brand .brand-name{font-size:12px;letter-spacing:.4px}
</style>
</head>
<body>

<!-- ========== OUTSIDE SPREAD ========== -->
<section class="spread spread-outside" aria-label="Brochure outside">
  <svg class="shapes" width="675" height="525" viewBox="0 0 675 525">
    <defs>
      <linearGradient id="hugGrad" x1="0" y1="0" x2="1" y2="1">
        <stop offset="0" stop-color="#c9c2b6"/>
        <stop offset=".45" stop-color="#9a6b45"/>
        <stop offset="1" stop-color="#7c8a93"/>
      </linearGradient>
      <linearGradient id="carGrad" x1="0" y1="0" x2="1" y2="1">
        <stop offset="0" stop-color="#f4f4f6"/>
        <stop offset=".45" stop-color="#b9bcc4"/>
        <stop offset="1" stop-color="#3a4467"/>
      </linearGradient>
      <clipPath id="photoTopClip"><rect x="330" y="0" width="345" height="525"/></clipPath>
      <clipPath id="greenArcClip"><rect x="330" y="120" width="345" height="200"/></clipPath>
      <polygon id="hexOut" points="30,0 60,17 60,51 30,68 0,51 0,17"/>
      <g id="icoChart" fill="none" stroke="#fff" stroke-width="1.4">
        <path d="M3 21V13h3v8M9 21V10h3v11M15 21V12h3v9M21 21V7"/>
        <path d="M2 21h21"/>
        <path d="M3 9l6-4 6 3 6-6"/>
        <circle cx="3" cy="9" r="1"/><circle cx="9" cy="5" r="1"/><circle cx="15" cy="8" r="1"/><circle cx="21" cy="2" r="1"/>
      </g>
      <g id="icoBank" fill="none" stroke="#fff" stroke-width="1.4">
        <path d="M2 8L12 2l10 6z"/><path d="M3 9h18M4 11v8M8 11v8M12 11v8M16 11v8M20 11v8M2 20h20M1 22h22"/>
      </g>
      <g id="icoCoin" fill="none" stroke="#fff" stroke-width="1.4">
        <circle cx="12" cy="12" r="10.5"/><circle cx="12" cy="12" r="7"/><path d="M10 8h3a2 2 0 010 4h-3zM10 12h3.5a2 2 0 010 4H10zM10 8v8"/>
      </g>
    </defs>

    <path d="M0,296 C80,282 160,305 200,355 C232,395 240,460 238,525 H0 Z" fill="var(--green)"/>
    <path d="M0,310 C80,298 150,325 185,370 C215,410 225,470 224,525 H0 Z" fill="url(#hugGrad)" role="img" aria-label="Photo: two people sharing a warm embrace"/>

    <path d="M222,101 C280,175 380,250 489,250 C590,250 665,170 675,64 V525 H222 Z" fill="var(--navy)"/>

    <g clip-path="url(#greenArcClip)">
      <ellipse cx="548" cy="58" rx="180" ry="194" fill="var(--green)"/>
    </g>
    <g clip-path="url(#photoTopClip)">
      <ellipse cx="540" cy="52" rx="172" ry="186" fill="url(#carGrad)" role="img" aria-label="Photo: smiling man in a suit leaning on a car"/>
    </g>

    <polygon points="338,210 356,220 356,240 338,250 320,240 320,220" fill="var(--green)"/>
    <text x="338" y="246" text-anchor="middle" fill="#fff" font-family="Montserrat, sans-serif" font-weight="800" font-size="30">“</text>

    <line x1="239" y1="428" x2="435" y2="428" stroke="#8f8dc0" stroke-width=".6"/>

    <g fill="none" stroke="#fff" stroke-width=".7">
      <path d="M250,437 a2.5,2.5 0 1 1 5,0 c0,2 -2.5,4.5 -2.5,4.5 s-2.5,-2.5 -2.5,-4.5z"/>
      <rect x="337" y="437" width="3.4" height="5" rx=".6"/>
      <rect x="336.6" y="446" width="4.4" height="3.2"/>
      <circle cx="338.8" cy="454" r="2.2"/>
    </g>

    <use href="#hexOut" x="457" y="264" fill="var(--green)"/>
    <use href="#hexOut" x="526" y="264" fill="var(--green)"/>
    <use href="#hexOut" x="595" y="264" fill="var(--green)"/>
    <use href="#hexOut" x="492" y="321" fill="var(--green)"/>
    <use href="#hexOut" x="560" y="321" fill="var(--green)"/>
    <use href="#icoCoin" transform="translate(475,277)"/>
    <use href="#icoBank" transform="translate(544,277)"/>
    <use href="#icoChart" transform="translate(613,274)"/>
    <use href="#icoChart" transform="translate(510,331)"/>
    <use href="#icoChart" transform="translate(578,331)"/>

    <line x1="445" y1="452" x2="669" y2="452" stroke="#8f8dc0" stroke-width=".6"/>
    <line x1="445" y1="473" x2="669" y2="473" stroke="#8f8dc0" stroke-width=".6"/>
  </svg>

  <h2 class="abs impact-title">THE IMPACT OF <span>YOUR GIFT</span></h2>
  <p class="abs impact-intro">Your generosity drives our mission.<br>With every Smart gift you’re supporting<br>Meadowlark and Allied Services.<br>Join our community of Smart Givers today<br>and make an enduring impact. With<br>Smart Giving your generosity reaches<br>further. Begin your Smart Giving journey<br>with us today.</p>
  <ul class="option-list">
    <li class="option" style="top:163px"><svg viewBox="0 0 10 10"><circle cx="5" cy="5" r="4.2" fill="none" stroke="#4cb748"/><path d="M3 5l1.5 1.5L7.5 3.5" fill="none" stroke="#4cb748"/></svg>Stocks and Securities</li>
    <li class="option" style="top:185px"><svg viewBox="0 0 10 10"><circle cx="5" cy="5" r="4.2" fill="none" stroke="#4cb748"/><path d="M3 5l1.5 1.5L7.5 3.5" fill="none" stroke="#4cb748"/></svg>DAFs</li>
    <li class="option" style="top:207px"><svg viewBox="0 0 10 10"><circle cx="5" cy="5" r="4.2" fill="none" stroke="#4cb748"/><path d="M3 5l1.5 1.5L7.5 3.5" fill="none" stroke="#4cb748"/></svg>QCDs</li>
    <li class="option" style="top:229px"><svg viewBox="0 0 10 10"><circle cx="5" cy="5" r="4.2" fill="none" stroke="#4cb748"/><path d="M3 5l1.5 1.5L7.5 3.5" fill="none" stroke="#4cb748"/></svg>Crypto</li>
    <li class="option" style="top:251px"><svg viewBox="0 0 10 10"><circle cx="5" cy="5" r="4.2" fill="none" stroke="#4cb748"/><path d="M3 5l1.5 1.5L7.5 3.5" fill="none" stroke="#4cb748"/></svg>Charitable Annuity</li>
  </ul>

  <div class="brand" style="left:278px;width:120px;top:14px"><span class="dot"></span><span class="brand-name">MEADOWLARK AND<br>ALLIED SERVICES</span></div>
  <p class="abs learn-more">To learn more about Smart Giving<br>Options and how they can benefit you<br>and Meadowlark and Allied Services,<br>please reach out to our team. We’re<br>here to help you navigate these<br>giving methods and answer<br>any question you<br>may have.</p>
  <p class="abs quote">Being kind to others is a way of<br>being good to yourself.</p>
  <p class="abs quote-author">Helen Marsh</p>
  <p class="abs will-lead">If you do not have a will</p>
  <p class="abs will-link">go to www.WillStarter.org</p>
  <p class="abs will-note">In 20 minutes you can have a</p>
  <p class="abs will-free">legal will – for free.</p>
  <div class="abs contact-btn">CONTACT US</div>
  <p class="abs question">Have more question?</p>
  <p class="abs question-note">Please contact us at Meadowlark and<br>Allied Services</p>
  <address class="abs contact-col" style="left:258px;font-style:normal">1250 Prairie View Rd.<br>Suite 4<br>Fargo, ND&nbsp; 58102</address>
  <p class="abs contact-col" style="left:345px">701-555-0148 (ext. 100)<br>info@meadowlarkallied.org<br>www.meadowlarkallied.org</p>
  <p class="abs follow">Follow us <i style="background:#4b6fc0"></i><i style="background:#d84b7d"></i></p>
  <p class="abs disclaimer">This material has been prepared for informational purposes only and is not intended to provide tax, accounting, or legal advice. Meadowlark and Allied Services is not a professional fiduciary organization. Please consult with your tax advisor or financial professional before making a decision about Smart Giving.</p>

  <div class="brand" style="left:440px;width:120px;top:14px"><span class="dot"></span><span class="brand-name">MEADOWLARK AND<br>ALLIED SERVICES</span></div>
  <span class="hex-label" style="left:457px;top:307px">Crypto</span>
  <span class="hex-label" style="left:526px;top:307px">DAF’s</span>
  <span class="hex-label" style="left:595px;top:304px">Stocks &amp;<br>Securities</span>
  <span class="hex-label" style="left:492px;top:361px">Stocks &amp;<br>Securities</span>
  <span class="hex-label" style="left:560px;top:361px">Stocks &amp;<br>Securities</span>
  <h1 class="abs transform">TRANSFORM</h1>
  <p class="abs your-giving">YOUR GIVING</p>
  <div class="abs mottos">
    <span><svg viewBox="0 0 14 14"><circle cx="7" cy="7" r="6" fill="none" stroke="#4cb748" stroke-width="1.2"/><path d="M4 7l2 2 4-4" fill="none" stroke="#4cb748" stroke-width="1.2"/></svg>Be Strategic</span>
    <span><svg viewBox="0 0 14 14"><circle cx="7" cy="7" r="6" fill="none" stroke="#4cb748" stroke-width="1.2"/><path d="M4 7l2 2 4-4" fill="none" stroke="#4cb748" stroke-width="1.2"/></svg>Be Smart</span>
  </div>
  <p class="abs discover">Discover the impact of Smart Giving with<br>Meadowlark and Allied Services</p>
</section>

<!-- ========== INSIDE SPREAD ========== -->
<section class="spread spread-inside" aria-label="Brochure inside">
  <svg class="shapes" width="677" height="526" viewBox="0 0 677 526">
    <defs>
      <linearGradient id="sailGrad" x1="0" y1="0" x2="0" y2="1">
        <stop offset="0" stop-color="#6fa5d6"/>
        <stop offset=".5" stop-color="#cfdbe6"/>
        <stop offset="1" stop-color="#2b5f8f"/>
      </linearGradient>
      <polygon id="hexIn" points="28,0 56,16 56,48 28,64 0,48 0,16"/>
      <g id="icoChartN" fill="none" stroke="#fff" stroke-width="1.3">
        <path d="M3 21V13h3v8M9 21V10h3v11M15 21V12h3v9M21 21V7"/><path d="M2 21h21"/>
        <path d="M3 9l6-4 6 3 6-6"/><circle cx="3" cy="9" r="1"/><circle cx="9" cy="5" r="1"/><circle cx="15" cy="8" r="1"/><circle cx="21" cy="2" r="1"/>
      </g>
      <g id="icoBankN" fill="none" stroke="#fff" stroke-width="1.3">
        <path d="M2 8L12 2l10 6z"/><path d="M3 9h18M4 11v8M8 11v8M12 11v8M16 11v8M20 11v8M2 20h20M1 22h22"/>
      </g>
      <g id="icoCoinN" fill="none" stroke="#fff" stroke-width="1.3">
        <circle cx="12" cy="12" r="10.5"/><circle cx="12" cy="12" r="7"/><path d="M10 8h3a2 2 0 010 4h-3zM10 12h3.5a2 2 0 010 4H10zM10 8v8"/>
      </g>
      <g id="icoGiftN" fill="none" stroke="#fff" stroke-width="1.3">
        <rect x="3" y="9" width="18" height="4"/><rect x="4.5" y="13" width="15" height="9"/><path d="M12 9v13M12 9c-3-6-8-4-6 0M12 9c3-6 8-4 6 0"/>
      </g>
      <g id="icoWatchN" fill="none" stroke="#fff" stroke-width="1.3">
        <circle cx="10" cy="13" r="8"/><path d="M10 13V8M8 3h4M10 3v2"/><circle cx="19" cy="18" r="4"/><path d="M19 16v4"/>
      </g>
    </defs>

    <rect x="223" y="0" width="223" height="526" fill="var(--paper-mid)"/>

    <path d="M0,0 H677 V60 C600,92 520,118 420,136 C340,150 270,160 200,160 C120,160 50,140 0,118 Z" fill="#ffffff"/>
    <path d="M30,0 H677 V58 C600,88 520,112 420,130 C340,144 270,152 200,152 C120,152 60,132 30,112 Z" fill="url(#sailGrad)" role="img" aria-label="Photo: senior couple relaxing on a sailboat at sea"/>
    <path d="M150,158 C300,168 440,150 520,120 C450,140 320,152 150,158 Z" fill="var(--green)"/>
    <path d="M180,160 C320,164 450,145 520,120 C480,150 330,172 180,168 Z" fill="var(--green)"/>

    <!-- headline badge -->
    <path d="M65,40 H214 a40,40 0 0 1 0,80 H96 L86,129 L78,120 H65 a40,40 0 0 1 0,-80 Z" fill="var(--navy)" stroke="#fff" stroke-width="2"/>

    <path d="M223,450 C290,405 380,405 446,450 V526 H223 Z" fill="#ffffff"/>
    <path d="M223,450 C290,400 380,400 446,450 C380,412 290,412 223,450 Z" fill="var(--green)"/>

    <use href="#hexIn" x="25" y="164" fill="var(--navy)"/>
    <use href="#icoChartN" transform="translate(41,183)"/>
    <use href="#hexIn" x="25" y="333" fill="var(--navy)"/>
    <use href="#icoBankN" transform="translate(41,353)"/>
    <use href="#hexIn" x="246" y="181" fill="var(--navy)"/>
    <circle cx="274" cy="213" r="14" fill="none" stroke="#fff" stroke-width="1"/>
    <use href="#icoCoinN" transform="translate(262,201)"/>
    <use href="#hexIn" x="467" y="146" fill="var(--navy)"/>
    <use href="#icoGiftN" transform="translate(483,165)"/>
    <use href="#hexIn" x="467" y="344" fill="var(--navy)"/>
    <use href="#icoWatchN" transform="translate(483,363)"/>

    <g fill="none" stroke="var(--green)" stroke-width=".9">
      <circle cx="246" cy="345" r="4.2"/><path d="M244,345 l1.5,1.5 l3,-3"/>
      <circle cx="246" cy="367" r="4.2"/><path d="M244,367 l1.5,1.5 l3,-3"/>
    </g>
  </svg>

  <p class="abs headline-number">5</p>
  <h1 class="abs headline-badge">STRATEGIC<br>AND SMART<br>WAYS</h1>

  <h2 class="way-title" style="left:93px;top:167px">Gifts of Stocks or<br>Appreciated Assets<br>Strategic &amp; Smart</h2>
  <p class="way-hint" style="left:93px;top:210px;width:110px">Consider your long-term publicly traded stock as a way to give to your favorite charity.</p>
  <p class="way-body" style="left:19px;top:238px;width:195px">You can make a significantly bigger impact when you donate long-term appreciated securities, including stock, mutual funds, and bonds, directly to your favorite charity.</p>
  <span class="how-pill" style="left:19px;top:267px">How Does It Work?</span>
  <p class="way-body" style="left:19px;top:283px;width:195px">When you donate stock to a charity, you will generally take a tax deduction for the full market value. Because you are donating stock, your contribution and tax deduction may be significantly higher than contributing the after-tax proceeds. The same benefits apply when you donate mutual funds or bonds.</p>

  <h2 class="way-title" style="left:93px;top:335px">Donor-Advised<br>Fund (DAF)<br>Strategic &amp; Smart</h2>
  <p class="way-hint" style="left:93px;top:378px;width:120px">Consider a DAF – a simple, flexible, and tax-advantageous way to give to your favorite charities.</p>
  <p class="way-body" style="left:19px;top:408px;width:195px">A Donor-Advised Fund (DAF), is like a charitable investment account for the sole purpose of supporting your favorite charities.</p>
  <span class="how-pill" style="left:19px;top:432px">How Does It Work?</span>
  <p class="way-body" style="left:19px;top:448px;width:198px">You establish a DAF and contribute cash, stocks, or non-publicly traded assets, cryptocurrency, and private company stock to be eligible for an immediate tax deduction. Those funds are contributed for tax-free growth. You can recommend grants be made from your DAF to any IRS qualified public charity.</p>

  <h2 class="way-title" style="left:314px;top:192px">Cryptocurrency<br>Strategic &amp; Smart</h2>
  <p class="way-hint" style="left:314px;top:222px;width:125px">Consider donating Bitcoin and other cryptocurrencies to your favorite charity.</p>
  <p class="way-body" style="left:240px;top:253px;width:198px">Bitcoin and other cryptocurrencies can be donated to charity just like other appreciated assets such as stocks and other business interests. Before you sell bitcoin and donate the after-tax proceeds, consider donating your bitcoin directly to a favorite charity.</p>
  <span class="how-pill" style="left:240px;top:294px">How Does It Work?</span>
  <p class="way-body" style="left:240px;top:311px;width:198px">Many donors find it useful to open a Donor-Advised Fund (DAF). This strategy includes two significant benefits, both for you and your favorite charity.</p>
  <p class="way-body" style="left:256px;top:338px;width:180px">Your tax deduction will be equal to the fair market value of the donated bitcoin (as determined by a qualified appraisal).</p>
  <p class="way-body" style="left:256px;top:360px;width:180px">Your cryptocurrency donation is tax-smart because it may eliminate capital gains taxes on the value / appreciation AND your favorite charity will receive 100% of the value of the contribution.</p>
  <p class="way-body" style="left:240px;top:395px;width:198px">Often charities are not able to accept direct donations of bitcoin/crypto so using a DAF is a great way to donate these assets.</p>

  <div class="brand inside-brand"><span class="dot"></span><span class="brand-name">MEADOWLARK AND ALLIED<br>SERVICES, INC.</span></div>

  <h2 class="way-title" style="left:535px;top:148px">Qualified Charitable<br>Distributions (QCDs)<br>Strategic &amp; Smart</h2>
  <p class="way-hint" style="left:535px;top:191px;width:130px">Consider a QCD – when planning your IRA withdrawal strategy...and donate to your favorite charity.</p>
  <p class="way-body" style="left:461px;top:218px;width:210px">IRA owners at age 70 ½ or over can transfer dollars from their IRA to charity tax-free each year. These transfers known as Qualified Charitable Distributions (QCDs) offer eligible older Americans a great way to easily give to charity.</p>
  <span class="how-pill" style="left:461px;top:255px">How Does It Work?</span>
  <p class="way-body" style="left:461px;top:272px;width:212px">Are you 72 and required to take a minimum distribution (RMD) from your IRA but do not need the funds? Consider a Qualified Charitable Distribution. Normally, distributions from a traditional IRA are taxable when received. With a QCD, these distributions become tax-free when paid directly from the IRA to your favorite eligible charity. An IRA owner wishing to make a QCD should contact their IRA trustee, allowing time to complete the transaction before the end of the year to receive the tax benefit.</p>

  <h2 class="way-title" style="left:535px;top:351px">Charitable Gift Annuity<br>Strategic &amp; Smart</h2>
  <p class="way-hint" style="left:535px;top:382px;width:120px">Consider establishing a Charitable Gift Annuity</p>
  <p class="way-body" style="left:461px;top:413px;width:210px">You make a donation to a single charity. The gift is set aside in a reserve account and invested.</p>
  <span class="how-pill" style="left:461px;top:435px">How Does It Work?</span>
  <p class="way-body" style="left:461px;top:452px;width:212px">A charitable gift annuity is a contract between a donor and a charity. As a donor, you make a sizable gift to charity using cash, securities, or possibly other assets. This money is then invested. In return, you become eligible to take a partial tax deduction for your donation, plus you receive a fixed stream of income from the charity for the rest of your life. At the end of your life (as well as your spouse’s, if you’re giving as a couple), the charity receives the remainder of the gift.</p>
</section>

</body>
</html>
```